Ridgeline Journeys business card

please see website
www.ridgelinejourneys.comau

info needed on card
Curtis Halvey
Ph
email
Adventure Riding GPS trails

please use my logo and colours off my site

Curtis Halvey
curtis@ridgelinejourneys.com

```html
<!DOCTYPE html>
<html lang="en">
<head>
<meta charset="utf-8">
<title>Ridgeline Journeys business card</title>
<link href="https://fonts.googleapis.com/css2?family=Source+Sans+3:ital,wght@0,400;0,600;0,700;1,400&display=swap" rel="stylesheet">
<style>
  :root {
    --backdrop: #4a4a4a;
    --card-light: #f6f6f6;
    --card-dark: #000000;
    --ink: #1c1c1c;
    --ink-soft: #444444;
    --rule: #bdbdbd;
    --accent: #f2e01c;
    --stitch: #6a6a6a;
  }
  * { margin: 0; padding: 0; box-sizing: border-box; }
  html, body { width: 1200px; height: 750px; overflow: hidden; }
  body {
    background: var(--backdrop);
    font-family: "Source Sans 3", Arial, sans-serif;
    position: relative;
  }
  .card {
    position: absolute;
    left: 371px;
    width: 461px;
    height: 263px;
    overflow: hidden;
  }
  .card--front { top: 99px; background: var(--card-light); }
  .card--back { top: 381px; background: var(--card-dark); }

  .brand {
    position: absolute;
    left: 38px;
    top: 136px;
    transform: translateY(-50%);
    display: flex;
    align-items: center;
    gap: 8px;
  }
  .brand__dot {
    width: 14px; height: 14px; border-radius: 50%;
    background: var(--accent);
    flex: none;
  }
  .brand__name {
    font-weight: 700;
    font-size: 17px;
    color: var(--ink);
    line-height: 1;
    letter-spacing: 0.2px;
    text-transform: uppercase;
  }
  .divider {
    position: absolute;
    left: 229px; top: 86px;
    width: 1px; height: 76px;
    background: var(--rule);
  }
  .contact {
    position: absolute;
    left: 245px; top: 80px;
  }
  .contact__name {
    font-weight: 600;
    font-size: 17px;
    color: var(--ink);
    margin-bottom: 8px;
  }
  .contact__row {
    display: flex;
    align-items: center;
    gap: 6px;
    font-size: 11.5px;
    color: var(--ink-soft);
    height: 17.5px;
  }
  .contact__row svg { width: 12px; height: 12px; flex: none; fill: var(--ink); }

  .stitch {
    position: absolute;
    left: 0; right: 0; top: 232px;
    height: 3px;
    background: repeating-linear-gradient(90deg, var(--stitch) 0 9px, transparent 9px 13px);
  }
  .tagline-band {
    position: absolute;
    left: 0; right: 0; top: 238px; bottom: 0;
    background: var(--card-dark);
    display: flex; align-items: center; justify-content: center;
  }
  .tagline {
    font-style: italic;
    font-size: 13px;
    color: var(--accent);
    letter-spacing: 0.2px;
  }

  .back-brand {
    position: absolute;
    left: 0; right: 0; top: 112px;
    display: flex; align-items: center; justify-content: center; gap: 10px;
  }
  .back-brand__dot {
    width: 22px; height: 22px; border-radius: 50%;
    background: var(--accent);
  }
  .back-brand__name {
    font-weight: 700;
    font-size: 26px;
    color: var(--accent);
    text-transform: uppercase;
    line-height: 1;
  }
  .back-url {
    position: absolute;
    left: 0; right: 0; top: 216px;
    text-align: center;
    font-style: italic;
    font-size: 12px;
    color: var(--accent);
  }
</style>
</head>
<body>
  <section class="card card--front">
    <div class="brand">
      <span class="brand__dot"></span>
      <span class="brand__name">Ridgeline Journeys</span>
    </div>
    <div class="divider"></div>
    <div class="contact">
      <p class="contact__name">Curtis Halvey</p>
      <p class="contact__row">
        <svg viewBox="0 0 24 24" aria-hidden="true"><path d="M6.6 10.8a15.2 15.2 0 0 0 6.6 6.6l2.2-2.2c.3-.3.7-.4 1-.2 1.1.4 2.3.6 3.6.6.6 0 1 .4 1 1V20c0 .6-.4 1-1 1A17 17 0 0 1 3 4c0-.6.4-1 1-1h3.5c.6 0 1 .4 1 1 0 1.3.2 2.5.6 3.6.1.3 0 .7-.2 1z"/></svg>
        612 408 7715
      </p>
      <p class="contact__row">
        <svg viewBox="0 0 24 24" aria-hidden="true"><path d="M2 5h20v14H2z M2 5l10 8 10-8" fill="none" stroke="#1c1c1c" stroke-width="2"/><path d="M3 6h18l-9 7z"/></svg>
        curtis@ridgelinejourneys.com
      </p>
      <p class="contact__row">
        <svg viewBox="0 0 24 24" aria-hidden="true"><circle cx="12" cy="12" r="10"/><path d="M7 8c2 0 3 1 3 3s-2 2-2 4M14 5c0 2 2 2 3 3s-1 3 1 4" fill="none" stroke="#f6f6f6" stroke-width="1.6"/></svg>
        www.ridgelinejourneys.comau
      </p>
    </div>
    <div class="stitch"></div>
    <div class="tagline-band"><p class="tagline">Adventure Riding GPS trails</p></div>
  </section>

  <section class="card card--back">
    <div class="back-brand">
      <span class="back-brand__dot"></span>
      <span class="back-brand__name">Ridgeline Journeys</span>
    </div>
    <p class="back-url">www.ridgelinejourneys.comau</p>
  </section>
</body>
</html>
```